New Business Card for Odd Fern Designs

I create and make jewellery and Clothing. But when it comes to business card design I fail completely.

Sketching is my area, drawing, putting things together neatly, not so much.

Here is a little blurb about my company:

Odd Fern Designs is a truly unique customer experience. Work one on one with Owner Petra Wolcott to make your costuming dreams come true.

Not after a costume? Browse through the store for a look at beautiful and unique piece of jewellery. Each piece has been put together by Petra, by hand. You'll find Steampunk, gothic, lolita and other quirky styles.

Want something else? What abotu a pair of warm kitty paws? A Pair of Kitty ears? A pony tail to wear on your jeans? There are so many options and things to choose! You will want to take it all home.

I have attached the previous business card with my mascot "Greta" As you can see there is a very Greta in Cloudmere feel to the overall company, with references to The Tin Tinker, and the idea that "We are all made here".

Colour's to use would be purple and blue. The winning design would show the unique but professional approach that Odd Fern Designs takes when creating each piece for their customers.

Reason: Wanted to give you a chance to go over feed back that has been sent out. I am committed to paying for the design that I will use. I think another week will help tweak things up.

Target Market(s)

Nerds, Geeks and Sci-Fi people aged 20 - 34 both Male and Female

Industry/Entity Type

Store

Requirements
Must have
• Website address: www.oddferndesigns.example

Yeah, rest is up too you!
Nice to have
• Honestly, if you could make the whole thing look like a Edwin Marlowe "Greta in Cloudmere" Drawing with the same line working style that would be amazing!

But I won't restrict you! I'd like to see what you can come up with.

```html
<!DOCTYPE html>
<html lang="en">
<head>
<meta charset="utf-8">
<title>Odd Fern Designs – Business Card</title>
<link rel="stylesheet" href="https://fonts.googleapis.com/css2?family=Ubuntu:wght@500;700&display=swap">
<style>
  :root {
    --page-bg: #e6e6ea;
    --card-paper: #f4f4f6;
    --card-paper-shade: #e3e3e8;
    --brand-purple: #4b2e86;
    --table-purple: #5b3a96;
    --brand-blue: #3a3fb5;
    --band-deep: #1e2a6e;
    --band-light: #3d6fb0;
    --ink: #2a2a2a;
    --mascot-top: #3a3a8c;
    --mascot-bottom: #4f86c6;
  }
  * { box-sizing: border-box; margin: 0; padding: 0; }
  html, body {
    width: 1200px; height: 861px; overflow: hidden;
    background: var(--page-bg);
    font-family: "Ubuntu", sans-serif;
  }
  .card-sheet { position: relative; width: 1200px; height: 861px; }
  .card {
    position: absolute; top: 275px;
    width: 540px; height: 310px;
    background: linear-gradient(160deg, var(--card-paper) 0%, #ffffff 45%, var(--card-paper-shade) 100%);
    box-shadow: 0 6px 18px rgba(0,0,0,.18);
    overflow: hidden;
  }
  .card--back { left: 40px; }
  .card--front { left: 620px; }
  .card__band { position: absolute; left: 0; width: 100%; }
  .card__band--top { top: 0; height: 30px; }
  .card__band--bottom { bottom: 0; height: 40px; }

  .mascot {
    position: absolute;
    background: linear-gradient(180deg, var(--mascot-top) 0%, #6a58b8 45%, var(--mascot-bottom) 100%);
    border-radius: 40% 40% 12px 12px;
    opacity: .85;
  }

  /* Back side */
  .back__logo {
    position: absolute; left: 28px; top: 38px;
    color: var(--brand-blue); font-weight: 700;
    font-size: 15px; letter-spacing: 2px; line-height: 1.1;
  }
  .back__title {
    position: absolute; left: 222px; top: 50px;
    font-weight: 700; font-size: 17px; color: var(--ink);
    letter-spacing: .3px;
  }
  .measure-table {
    position: absolute; left: 58px; top: 82px;
    width: 450px; border-collapse: collapse; table-layout: fixed;
    color: var(--table-purple); font-weight: 700; font-size: 11.5px;
  }
  .measure-table td {
    border: 2px solid var(--table-purple);
    height: 20px; padding: 0 5px;
    white-space: nowrap; overflow: hidden;
  }
  .measure-table .label { width: 112px; }
  .measure-table .value { width: 113px; }
  .measure-table .label--small { font-size: 8.5px; line-height: 1; white-space: normal; }
  .mascot--small { left: 6px; bottom: 44px; width: 48px; height: 80px; }

  /* Front side */
  .mascot--large { left: 22px; top: 46px; width: 240px; height: 236px; }
  .front__logo {
    position: absolute; right: 30px; top: 56px; text-align: right;
    color: var(--brand-blue); font-weight: 700; line-height: 1.05;
  }
  .front__logo-main { display: block; font-size: 30px; letter-spacing: 4px; }
  .front__logo-sub { display: block; font-size: 20px; letter-spacing: 7px; }
  .front__tagline {
    position: absolute; right: 30px; top: 140px; width: 225px;
    text-align: center; font-size: 10px; color: var(--ink); line-height: 1.35;
  }
  .front__name {
    position: absolute; right: 32px; top: 176px;
    font-size: 26px; font-weight: 700; color: var(--brand-purple);
  }
  .contact {
    position: absolute; right: 30px; list-style: none;
    font-size: 13px; color: var(--ink); font-weight: 500;
  }
  .contact li { display: flex; align-items: center; justify-content: flex-end; gap: 6px; margin-bottom: 8px; }
  .contact svg { width: 18px; height: 18px; }
  .contact--list { top: 220px; }
</style>
</head>
<body>
<main class="card-sheet">

  <section class="card card--back" aria-label="Card back: costume measurements">
    <svg class="card__band card__band--top" viewBox="0 0 540 30" preserveAspectRatio="none" aria-hidden="true">
      <defs><linearGradient id="topBandBack" x1="0" x2="1"><stop offset="0" stop-color="#8d8fd8"/><stop offset=".5" stop-color="var(--brand-blue)"/><stop offset="1" stop-color="var(--band-deep)"/></linearGradient></defs>
      <polygon points="0,0 540,0 540,22 380,16 200,12 0,10" fill="url(#topBandBack)"/>
    </svg>

    <div class="back__logo">ODD FERN<br>DESIGNS</div>
    <h2 class="back__title">COSTUME MEASUREMENTS</h2>

    <table class="measure-table">
      <tr><td class="label">BUST</td><td class="value"></td><td class="label">WRIST</td><td class="value"></td></tr>
      <tr><td class="label">WAIST</td><td class="value"></td><td class="label">UPPER ARM</td><td class="value"></td></tr>
      <tr><td class="label">HIPS</td><td class="value"></td><td class="label">CALF</td><td class="value"></td></tr>
      <tr><td class="label">BACK WIDTH</td><td class="value"></td><td class="label">ANKLE</td><td class="value"></td></tr>
      <tr><td class="label">FRONT CHEST</td><td class="value"></td><td class="label">NAPE TO WAIST</td><td class="value"></td></tr>
      <tr><td class="label">SHOULDER</td><td class="value"></td><td class="label">WAIST TO HIP</td><td class="value"></td></tr>
      <tr><td class="label">NECK SIZE</td><td class="value"></td><td class="label label--small">FRONT SHOULDER<br>TO WAIST</td><td class="value"></td></tr>
      <tr><td class="label">SLEEVE</td><td class="value"></td><td class="label">OUTSIDE LEG</td><td class="value"></td></tr>
      <tr><td class="label">UNDER BUST</td><td class="value"></td><td class="label">INSIDE LEG</td><td class="value"></td></tr>
    </table>

    <div class="mascot mascot--small" role="img" aria-label="Small illustration of the mascot Greta in a top hat, sitting"></div>

    <svg class="card__band card__band--bottom" viewBox="0 0 540 40" preserveAspectRatio="none" aria-hidden="true">
      <defs><linearGradient id="bottomBandBack" x1="0" x2="1"><stop offset="0" stop-color="var(--band-light)"/><stop offset="1" stop-color="var(--band-deep)"/></linearGradient></defs>
      <polygon points="0,40 0,36 540,16 540,24 60,40" fill="url(#bottomBandBack)"/>
    </svg>
  </section>

  <section class="card card--front" aria-label="Card front: contact details">
    <svg class="card__band card__band--top" viewBox="0 0 540 30" preserveAspectRatio="none" aria-hidden="true">
      <defs><linearGradient id="topBandFront" x1="0" x2="1"><stop offset="0" stop-color="#8d8fd8"/><stop offset=".5" stop-color="var(--brand-blue)"/><stop offset="1" stop-color="var(--band-deep)"/></linearGradient></defs>
      <polygon points="0,0 540,0 540,22 380,16 200,12 0,10" fill="url(#topBandFront)"/>
    </svg>

    <div class="mascot mascot--large" role="img" aria-label="Illustration of the mascot Greta in a top hat, purple shirt and jeans, sitting on the floor"></div>

    <div class="front__logo">
      <span class="front__logo-main">ODD FERN</span>
      <span class="front__logo-sub">DESIGNS</span>
    </div>

    <p class="front__tagline">• Steampunk Jewelry • kitty ears • paws •<br>tails • custom costumes • lolita •</p>

    <h1 class="front__name">Petra Wolcott</h1>

    <ul class="contact contact--list">
      <li>petra@oddferndesigns.example
        <svg viewBox="0 0 18 18" aria-hidden="true"><circle cx="9" cy="9" r="8" fill="none" stroke="var(--ink)" stroke-width="1.5"/><rect x="4.5" y="6" width="9" height="6" fill="none" stroke="var(--ink)" stroke-width="1.2"/><polyline points="4.5,6 9,9.5 13.5,6" fill="none" stroke="var(--ink)" stroke-width="1.2"/></svg>
      </li>
      <li>www.oddferndesigns.example
        <svg viewBox="0 0 18 18" aria-hidden="true"><circle cx="9" cy="9" r="8" fill="none" stroke="var(--ink)" stroke-width="1.5"/><rect x="4.5" y="5" width="9" height="6" fill="none" stroke="var(--ink)" stroke-width="1.2"/><line x1="6.5" y1="13" x2="11.5" y2="13" stroke="var(--ink)" stroke-width="1.2"/></svg>
      </li>
    </ul>

    <svg class="card__band card__band--bottom" viewBox="0 0 540 40" preserveAspectRatio="none" aria-hidden="true">
      <defs><linearGradient id="bottomBandFront" x1="0" x2="1"><stop offset="0" stop-color="var(--band-light)"/><stop offset="1" stop-color="var(--band-deep)"/></linearGradient></defs>
      <polygon points="0,40 0,36 540,16 540,24 60,40" fill="url(#bottomBandFront)"/>
    </svg>
  </section>

</main>
</body>
</html>
```